Roofing Contractor business card redesign

I want to redesign my business card with a fresh, eye catching concept

Target Market(s)

Residential Roofing Clients, potential employees, and subcontractors.

Industry/Entity Type

Business

Colors

Designer to choose colors to be used in the design.

Requirements
Nice to have
• I just want something that's more pleasing to the eye. You can use a combination of either / or of my logos.

```html
<!DOCTYPE html>
<html lang="en">
<head>
<meta charset="utf-8">
<title>Steady Hands Contractors – Business Card</title>
<link rel="stylesheet" href="https://fonts.googleapis.com/css2?family=Oswald:wght@600&family=Roboto:wght@400;500&display=swap">
<style>
  :root {
    --backdrop: #e4ddd3;
    --card: #f1f0ee;
    --card-edge: #d9d7d3;
    --ink: #2a1d17;
    --ink-soft: #3b302b;
    --accent: #b8481f;
    --mark-fill: #e6c9a8;
  }
  * { margin: 0; padding: 0; box-sizing: border-box; }
  html, body { width: 1200px; height: 969px; overflow: hidden; }
  body {
    background: var(--backdrop);
    font-family: "Roboto", Arial, sans-serif;
    color: var(--ink);
    position: relative;
  }
  .card {
    position: absolute;
    left: 100px; top: 199px;
    width: 1000px; height: 571px;
    background: var(--card);
    border: 2px solid var(--card-edge);
    border-radius: 28px;
    box-shadow: 0 10px 30px rgba(60, 40, 25, 0.15);
  }
  .brand-mark {
    position: absolute;
    left: 35px; top: 96px;
    width: 430px; height: 430px;
    border-radius: 50%;
    background: var(--mark-fill);
    display: flex; align-items: center; justify-content: center;
  }
  .brand-mark-name {
    font-family: "Oswald", "Arial Narrow", sans-serif;
    font-weight: 600;
    font-size: 54px;
    color: var(--ink);
    white-space: nowrap;
  }
  .details {
    position: absolute;
    right: 47px; top: 0;
    text-align: right;
    width: 520px;
  }
  .line { position: absolute; right: 0; white-space: nowrap; }
  .company-name {
    top: 42px;
    font-family: "Oswald", "Arial Narrow", sans-serif;
    font-weight: 600;
    font-size: 70px; line-height: 84px;
    color: var(--ink);
    letter-spacing: -0.5px;
  }
  .company-sub { top: 132px; font-weight: 500; font-size: 24px; color: var(--ink); }
  .person-name { top: 206px; font-weight: 500; font-size: 31px; letter-spacing: 0.5px; color: var(--ink); }
  .credential { font-size: 25px; color: var(--accent); }
  .credential.first { top: 246px; }
  .credential.second { top: 279px; }
  .address { font-size: 24px; color: var(--ink-soft); }
  .address.first { top: 320px; }
  .address.second { top: 354px; }
  .contact {
    font-size: 24px; color: var(--ink-soft);
    display: flex; align-items: center; gap: 12px;
  }
  .contact svg { width: 20px; height: 20px; fill: var(--ink); }
  .contact.phone { top: 397px; }
  .contact.mobile { top: 430px; }
  .contact.email { top: 462px; }
  .contact.web { top: 494px; }
</style>
</head>
<body>
  <div class="card">
    <div class="brand-mark" role="img" aria-label="Company mark area">
      <span class="brand-mark-name">Steady Hands</span>
    </div>

    <div class="details">
      <div class="line company-name">Steady Hands</div>
      <div class="line company-sub">Contractors, Inc.</div>
      <div class="line person-name">MARK DELANEY</div>
      <div class="line credential first">Halden Certified Roof Inspector</div>
      <div class="line credential second">Licensed Property Adjuster</div>
      <div class="line address first">4410 Cedar Ridge Drive Suite 118</div>
      <div class="line address second">Plano, TX 75093</div>

      <div class="line contact phone">(555) 210-4800
        <svg viewBox="0 0 24 24" aria-hidden="true"><path d="M6.6 10.8a15.1 15.1 0 0 0 6.6 6.6l2.2-2.2a1 1 0 0 1 1-.25 11.4 11.4 0 0 0 3.6.57 1 1 0 0 1 1 1V20a1 1 0 0 1-1 1A17 17 0 0 1 3 4a1 1 0 0 1 1-1h3.5a1 1 0 0 1 1 1c0 1.25.2 2.45.57 3.57a1 1 0 0 1-.25 1z"/></svg>
      </div>
      <div class="line contact mobile">(555) 318-2247
        <svg viewBox="0 0 24 24" aria-hidden="true"><path d="M7 2h10a2 2 0 0 1 2 2v16a2 2 0 0 1-2 2H7a2 2 0 0 1-2-2V4a2 2 0 0 1 2-2zm0 3v13h10V5zm5 14.2a1 1 0 1 0 0 .01z"/></svg>
      </div>
      <div class="line contact email">mark@steadyhandstx.com
        <svg viewBox="0 0 24 24" aria-hidden="true"><path d="M3 5h18a1 1 0 0 1 1 1v12a1 1 0 0 1-1 1H3a1 1 0 0 1-1-1V6a1 1 0 0 1 1-1zm1 2.2V17h16V7.2l-8 5.3z"/></svg>
      </div>
      <div class="line contact web">www.steadyhandstx.com
        <svg viewBox="0 0 24 24" aria-hidden="true"><path d="M12 2a10 10 0 1 0 0 20 10 10 0 0 0 0-20zm-1 17.9A8 8 0 0 1 4.1 11H7c.1 2.9.9 5.5 2 7.3zm0-8.9h-2c.1-2.5.8-4.6 2-6.1zm2-6.1c1.2 1.5 1.9 3.6 2 6.1h-2zM13 13h2c-.1 2.5-.8 4.6-2 6.1zm2 5.3c1.1-1.8 1.9-4.4 2-7.3h2.9a8 8 0 0 1-4.9 7.3z"/></svg>
      </div>
    </div>
  </div>
</body>
</html>
```